Fast Growing Personal Injury Law Firm Needs Business Card Design

We need a business card design for a fast growing personal injury law firm in Florida. Our name is Dorian Kalvenfeld, P.A. Our practice is comprised of younger attorneys (in their 30s) that employ more modern techniques/tools than our older competition. We would prefer a look that is a modern play on a classic look. Also, we would like to continue using a color scheme that employs navy blue and kelly green (other shades of green could be fine too) as well as our "E" logo.

Industry/Entity Type

Law Firm

```html
<!DOCTYPE html>
<html lang="en">
<head>
<meta charset="utf-8">
<title>Dorian Kalvenfeld, P.A. — Business Card</title>
<link rel="stylesheet" href="https://fonts.googleapis.com/css2?family=Cinzel:wght@500&family=Lato:wght@400&display=swap">
<style>
  :root {
    --navy: #0f2a5c;
    --green: #158a44;
    --ink: #3c3c3c;
    --rule: #c9c9c9;
    --paper: #ffffff;
    --backdrop: #5c5c5c;
  }
  html, body {
    margin: 0;
    padding: 0;
    width: 1200px;
    height: 820px;
    overflow: hidden;
    background: var(--backdrop);
    font-family: "Lato", Arial, sans-serif;
  }
  .stage { position: relative; width: 1200px; height: 820px; }
  .card {
    position: absolute;
    width: 477px;
    height: 274px;
    background: var(--paper);
    overflow: hidden;
  }
  .card--front { left: 115px; top: 257px; }
  .card--back { left: 621px; top: 257px; border-top: 2px solid var(--navy); height: 272px; }

  .brand { position: absolute; display: flex; align-items: center; gap: 13px; }
  .brand__mark { width: 64px; height: 60px; background: var(--navy); flex: none; }
  .brand__text { display: flex; flex-direction: column; }
  .brand__name {
    font-family: "Cinzel", Georgia, serif;
    font-weight: 500;
    font-size: 19px;
    color: var(--navy);
    letter-spacing: 0.4px;
    line-height: 1.1;
    padding-bottom: 4px;
    border-bottom: 1.5px solid var(--navy);
    white-space: nowrap;
  }
  .brand__tagline {
    font-family: "Cinzel", Georgia, serif;
    font-weight: 500;
    font-size: 14px;
    color: var(--green);
    letter-spacing: 1.6px;
    margin-top: 3px;
    white-space: nowrap;
  }
  .card--front .brand { left: 50px; top: 43px; }
  .card--back .brand { left: 60px; top: 110px; }

  .person { position: absolute; left: 50px; top: 146px; width: 182px; }
  .person__name { font-size: 16.5px; color: var(--navy); line-height: 1.2; }
  .person__title {
    font-size: 12.5px; color: var(--navy);
    padding: 3px 0 3px; border-bottom: 1px solid var(--navy);
  }
  .person__address { font-size: 12.5px; color: #222; line-height: 17px; margin-top: 6px; white-space: nowrap; }

  .divider { position: absolute; left: 254px; top: 150px; width: 1px; height: 80px; background: var(--rule); }

  .contact { position: absolute; left: 280px; top: 146px; margin: 0; padding: 0; list-style: none; }
  .contact li { display: flex; align-items: center; gap: 5px; font-size: 12.5px; color: var(--ink); height: 20px; }
  .contact svg { width: 11px; height: 11px; flex: none; }

  .footer-band { position: absolute; left: 0; bottom: 0; width: 477px; height: 17px; }
</style>
</head>
<body>
<main class="stage">

  <section class="card card--front" aria-label="Card front">
    <div class="brand">
      <span class="brand__mark"></span>
      <div class="brand__text">
        <span class="brand__name">Dorian Kalvenfeld, P.A.</span>
        <span class="brand__tagline">Personal Injury Attorneys</span>
      </div>
    </div>

    <div class="person">
      <div class="person__name">Dorian Kalvenfeld</div>
      <div class="person__title">Attorney at Law</div>
      <div class="person__address">2150 Harborview Drive Suite 400<br>Palmetto Bay, Florida 34100</div>
    </div>

    <span class="divider"></span>

    <ul class="contact">
      <li>
        <svg viewBox="0 0 12 12"><circle cx="6" cy="6" r="6" fill="var(--navy)"/><path d="M4 3.2l1 1.4-.6.7c.4.9 1 1.5 1.9 1.9l.7-.6 1.4 1-.5 1c-2.3-.3-4-2-4.3-4.3z" fill="#fff"/></svg>
        555.214.0187
      </li>
      <li>
        <svg viewBox="0 0 12 12"><circle cx="6" cy="6" r="6" fill="var(--navy)"/><rect x="3.6" y="3" width="4.8" height="6" rx="0.6" fill="#fff"/><rect x="4.3" y="3.8" width="3.4" height="1.8" fill="var(--navy)"/></svg>
        555.214.0192
      </li>
      <li>
        <svg viewBox="0 0 12 12"><circle cx="6" cy="6" r="6" fill="var(--navy)"/><rect x="3" y="4" width="6" height="4" fill="#fff"/><path d="M3 4l3 2.2L9 4" stroke="var(--navy)" stroke-width="0.7" fill="none"/></svg>
        dorian@kalvenfeldlaw.com
      </li>
      <li>
        <svg viewBox="0 0 12 12"><circle cx="6" cy="6" r="6" fill="var(--navy)"/><circle cx="6" cy="6" r="3.3" fill="none" stroke="#fff" stroke-width="0.8"/><path d="M2.7 6h6.6M6 2.7v6.6" stroke="#fff" stroke-width="0.7"/></svg>
        www.kalvenfeldlaw.com
      </li>
    </ul>

    <svg class="footer-band" viewBox="0 0 477 17" preserveAspectRatio="none" aria-hidden="true">
      <rect x="0" y="10" width="477" height="7" fill="var(--navy)"/>
      <polygon points="254,0 477,0 477,17 240,17" fill="var(--navy)"/>
      <polygon points="0,0 250,0 241,9 0,9" fill="var(--green)"/>
    </svg>
  </section>

  <section class="card card--back" aria-label="Card back">
    <div class="brand">
      <span class="brand__mark"></span>
      <div class="brand__text">
        <span class="brand__name">Dorian Kalvenfeld, P.A.</span>
        <span class="brand__tagline">Personal Injury Attorneys</span>
      </div>
    </div>
  </section>

</main>
</body>
</html>
```